Stunning Podcast Cover Design for The Morning Tide Hour!!

I need a design for my new podcast.
I will need it in a variety of size/formats, such as a large version for my podcast website homepage, the thumbnail for Tunebay, Castloft, Vexa Store and more.

The podcast is called "The Morning Tide Hour" and it includes topics such as: business, entrepreneurship, finance, budgeting, estate planning, end-of-life planning, travel, business and personal stories featuring people from all over the world, life in general, and more.

I don't have a vision in mind so am looking for creativity but it definitely needs to have the colour gold in it somewhere! No cartoon characters please.

I will provide comments/feedback to each designer.

***UPDATE: Please see some photos of me that can be used in the podcast design.

Here is some tips on creating podcast designs. https://www.castbrindle.example/blog/10-tips-create-awesome-podcast-artwork

Target Market(s)

Adults 25 - 65

Font styles to use
Other font styles liked:
• something modern - see my company logo as an example

Colors

Designer to choose colors to be used in the design.

Requirements
Must have
• The colour gold in it
Nice to have
• I feel like the word "The" should be smaller then the other three words.
• I would like to see designs with a white coloured background and a black coloured one also...
• Perhaps designs with a filter over the photo, and without.
• Perhaps use my photo, or don't use my photo!
• Please see some photos of me that can be used in the podcast design.
• Here is some tips on creating podcast designs. https://www.castbrindle.example/blog/10-tips-create-awesome-podcast-artwork
Should not have
• cartoon characters
• Corny 1990's "Evenings with the Grand and Glittering" look - see https://www.viddlewave.example/watch?v=Q7T2KX8PLMD

```html
<!DOCTYPE html>
<html lang="en">
<head>
<meta charset="utf-8">
<title>The Morning Tide Hour</title>
<link rel="stylesheet" href="https://fonts.googleapis.com/css2?family=Playfair+Display:wght@400;500&display=swap">
<style>
  :root {
    --sky-top: #352640;
    --sky-mauve: #8e6384;
    --sky-rose: #b9616f;
    --horizon: #e0704c;
    --sun: #fff1c4;
    --water: #8d4a6a;
    --water-deep: #4a2a40;
    --shore: #140c12;
    --title-white: #ffffff;
    --gold-light: #f6dc8c;
    --gold-mid: #d6a63c;
    --gold-deep: #a9741e;
  }
  html, body {
    margin: 0;
    padding: 0;
    width: 1200px;
    height: 1200px;
    overflow: hidden;
    background: var(--shore);
  }
  .cover {
    position: relative;
    width: 1200px;
    height: 1200px;
    overflow: hidden;
    font-family: "Playfair Display", "Didot", serif;
  }
  .cover__scene {
    position: absolute;
    inset: 0;
    background:
      radial-gradient(circle at 600px 550px, var(--sun) 0, rgba(255, 200, 120, 0.85) 18px, rgba(240, 130, 70, 0.45) 90px, rgba(224, 112, 76, 0) 260px),
      linear-gradient(to bottom,
        var(--sky-top) 0%,
        var(--sky-mauve) 22%,
        var(--sky-rose) 38%,
        var(--horizon) 50%,
        var(--water) 60%,
        var(--water-deep) 78%,
        var(--shore) 100%);
  }
  .cover__title {
    position: absolute;
    inset: 0;
    margin: 0;
    font-weight: 400;
    text-align: center;
    color: var(--title-white);
    text-shadow: 0 2px 6px rgba(40, 10, 30, 0.35);
  }
  .title__line {
    position: absolute;
    left: 0;
    right: 0;
    display: block;
    line-height: 1;
  }
  .title__article {
    top: 236px;
    font-size: 84px;
    letter-spacing: 2px;
  }
  .title__word--first {
    top: 318px;
    font-size: 180px;
    letter-spacing: -2px;
  }
  .title__word--second {
    top: 518px;
    font-size: 222px;
  }
  .title__word--accent {
    top: 722px;
    font-size: 222px;
    background: linear-gradient(100deg, var(--gold-deep) 0%, var(--gold-light) 30%, var(--gold-mid) 55%, var(--gold-light) 75%, var(--gold-deep) 100%);
    -webkit-background-clip: text;
    background-clip: text;
    color: transparent;
    text-shadow: none;
    filter: drop-shadow(0 2px 5px rgba(40, 10, 30, 0.35));
  }
</style>
</head>
<body>
  <main class="cover">
    <div class="cover__scene" role="img" aria-label="Photograph of a sunset over a calm bay with small wooded islands and a dark shoreline village"></div>
    <h1 class="cover__title">
      <span class="title__line title__article">THE</span>
      <span class="title__line title__word--first">MORNING</span>
      <span class="title__line title__word--second">TIDE</span>
      <span class="title__line title__word--accent">HOUR</span>
    </h1>
  </main>
</body>
</html>
```